Pharmacy ad

need 2 pharmacy ads for the phone book. one for Brookvale Pharmacy and one for Cedarline Care Pharmacy. Dimensions for ad is 4.75in x 4.667 in. please see attached examples of ad uploaded as well logos of each pharmacy

```html
<!DOCTYPE html>
<html lang="en">
<head>
<meta charset="utf-8">
<title>Cedarline Care Pharmacy – Directory Ad</title>
<link rel="stylesheet" href="https://fonts.googleapis.com/css2?family=Anton&family=Dosis:wght@500&family=Kaushan+Script&family=Montserrat:wght@700;800&family=Raleway:wght@500;700&family=Roboto+Condensed:wght@300&display=swap">
<style>
  :root {
    --brand-blue: #3d4fa3;
    --brand-green: #6cbf45;
    --band-green: #c2e29a;
    --ink: #111111;
    --white: #ffffff;
  }
  * { margin: 0; padding: 0; box-sizing: border-box; }
  html, body { width: 1200px; height: 1180px; overflow: hidden; background: var(--white); }
  .ad { position: relative; width: 1200px; height: 1180px; overflow: hidden; background: var(--white); }

  .hero-photo {
    position: absolute; left: 0; top: 0; width: 1200px; height: 470px;
    background: linear-gradient(100deg, #f4f5f6 0%, #e7e9ea 40%, #d9d4cf 62%, #b68b6a 78%, #5a3a26 92%, #3b2618 100%);
  }
  .waves { position: absolute; left: 0; top: 0; }

  .brand { position: absolute; left: 62px; top: 72px; display: flex; align-items: center; gap: 26px; }
  .brand-dot { width: 150px; height: 150px; border-radius: 50%; background: var(--brand-blue); }
  .brand-name { font-family: "Montserrat", sans-serif; font-weight: 800; color: var(--brand-blue); text-align: center; }
  .brand-name .line-main { display: block; font-size: 66px; line-height: 1; letter-spacing: -1px; }
  .brand-name .line-sub { display: flex; align-items: center; gap: 10px; font-size: 40px; line-height: 1.2; margin-top: 6px; }
  .brand-name .line-sub::before, .brand-name .line-sub::after { content: ""; flex: 1; height: 3px; background: var(--brand-green); }

  .accepts { position: absolute; left: 166px; top: 274px; }
  .accepts-label { font-family: "Montserrat", sans-serif; font-weight: 700; font-size: 24px; color: var(--ink); }
  .accepts-list { display: flex; gap: 24px; margin-top: 8px; }
  .partner { height: 55px; background: var(--white); display: flex; align-items: center; justify-content: center;
    font-family: "Montserrat", sans-serif; font-weight: 700; font-size: 16px; color: var(--brand-blue); padding: 0 10px; }
  .partner.wide { width: 268px; font-size: 20px; }

  .tagline { position: absolute; left: 0; top: 455px; width: 1200px; text-align: center;
    font-family: "Kaushan Script", cursive; font-size: 104px; color: var(--brand-blue); line-height: 1.2; }

  .offers { position: absolute; left: 122px; top: 652px; }
  .offer { display: flex; align-items: flex-start; height: 108px; }
  .offer-rate { font-family: "Anton", sans-serif; font-size: 106px; line-height: 0.88; color: var(--brand-blue);
    width: 198px; flex: none; letter-spacing: -6px; white-space: nowrap; }
  .offer-text { padding-top: 10px; }
  .offer-title { font-family: "Roboto Condensed", sans-serif; font-weight: 300; font-size: 52px; line-height: 0.9; color: var(--brand-blue); }
  .offer-detail { font-family: "Anton", sans-serif; font-size: 26px; line-height: 1.05; color: var(--brand-blue);
    text-transform: uppercase; letter-spacing: 1.8px; margin-top: 2px; }

  .divider { position: absolute; left: 585px; top: 664px; width: 5px; height: 298px; background: var(--brand-green); }

  .services { position: absolute; top: 682px; list-style: none; font-family: "Dosis", sans-serif; font-weight: 500; font-size: 30px; line-height: 1; color: var(--brand-blue); }
  .services li { position: absolute; left: 0; padding-left: 24px; white-space: nowrap; }
  .services li::before { content: ""; position: absolute; left: 0; top: 11px; width: 10px; height: 10px; border-radius: 50%; background: var(--brand-blue); }
  .services.col-a { left: 613px; }
  .services.col-b { left: 899px; }

  .footer { position: absolute; left: 0; top: 981px; width: 1200px; height: 199px; background: var(--brand-green); }
  .contact { position: absolute; font-family: "Raleway", sans-serif; font-weight: 700; font-size: 30px; color: var(--ink); display: flex; align-items: center; gap: 14px; white-space: nowrap; }
  .contact svg { flex: none; }
  .contact.address { left: 62px; top: 20px; }
  .contact.email { left: 62px; top: 68px; }
  .contact.phone { left: 576px; top: 68px; letter-spacing: 1.5px; }
  .hours { position: absolute; left: 64px; top: 124px; font-family: "Montserrat", sans-serif; font-weight: 800; font-size: 44px; color: var(--ink); letter-spacing: -0.5px; white-space: nowrap; }
  .social { position: absolute; left: 980px; top: 22px; width: 200px; text-align: center; }
  .social-label { font-family: "Raleway", sans-serif; font-weight: 500; font-size: 26px; color: #1d2a55; }
  .social-link { display: flex; align-items: center; justify-content: center; gap: 10px; margin-top: 30px;
    font-family: "Raleway", sans-serif; font-weight: 700; font-size: 22px; color: var(--brand-blue); }
  .social-dot { width: 44px; height: 44px; border-radius: 50%; background: var(--brand-blue); }
</style>
</head>
<body>
<div class="ad">
  <div class="hero-photo" role="img" aria-label="Photo of a smiling pharmacist in glasses reading a medicine box label"></div>

  <svg class="waves" width="1200" height="1180" viewBox="0 0 1200 1180" aria-hidden="true">
    <path d="M0,345 C320,440 760,470 1200,330 L1200,640 C820,590 360,600 0,670 Z" fill="var(--band-green)"/>
    <path d="M0,345 C320,440 760,470 1200,330 L1200,342 C760,480 320,452 0,360 Z" fill="var(--brand-green)"/>
    <path d="M560,440 C800,438 1000,400 1200,340 L1200,352 C1000,420 800,448 560,440 Z" fill="var(--brand-blue)"/>
    <path d="M0,670 C360,600 820,590 1200,640 L1200,1180 L0,1180 Z" fill="var(--white)"/>
    <path d="M0,660 C360,590 820,580 1200,620 L1200,646 C820,598 360,606 0,672 Z" fill="var(--brand-green)"/>
    <path d="M250,610 C560,582 900,588 1200,640 L1200,668 C900,606 560,598 250,610 Z" fill="var(--brand-blue)"/>
  </svg>

  <div class="brand">
    <div class="brand-dot"></div>
    <div class="brand-name">
      <span class="line-main">Cedarline Care</span>
      <span class="line-sub">PHARMACY</span>
    </div>
  </div>

  <div class="accepts">
    <div class="accepts-label">WE ACCEPT:</div>
    <div class="accepts-list">
      <div class="partner">Payvia</div>
      <div class="partner">Cardmax</div>
      <div class="partner">Sunrise Life</div>
      <div class="partner wide">Harbourline Insurance</div>
    </div>
  </div>

  <div class="tagline">Where good health begins</div>

  <div class="offers">
    <div class="offer">
      <div class="offer-rate">10%</div>
      <div class="offer-text">
        <div class="offer-title">DISCOUNT</div>
        <div class="offer-detail">On senior citizen</div>
      </div>
    </div>
    <div class="offer">
      <div class="offer-rate">10%</div>
      <div class="offer-text">
        <div class="offer-title">DISCOUNT</div>
        <div class="offer-detail">On student with<br>valid ID card</div>
      </div>
    </div>
    <div class="offer">
      <div class="offer-rate">10%</div>
      <div class="offer-text">
        <div class="offer-title">DISCOUNT</div>
        <div class="offer-detail">On hospital<br>prescriptions</div>
      </div>
    </div>
  </div>

  <div class="divider"></div>

  <ul class="services col-a">
    <li style="top:0">Certified Pharmacists</li>
    <li style="top:57px">Affordable prices</li>
    <li style="top:114px">Brand and<br>Generic Medicines</li>
    <li style="top:201px">Blood Pressure and<br>Glucose checks</li>
  </ul>
  <ul class="services col-b">
    <li style="top:0">Personal care and<br>Beauty Products</li>
    <li style="top:87px">Injectables</li>
    <li style="top:151px">Special Orders</li>
    <li style="top:215px">Delivery service</li>
  </ul>

  <footer class="footer">
    <div class="contact address">
      <svg width="30" height="40" viewBox="0 0 30 40" aria-hidden="true"><path d="M15,0 C6.7,0 0,6.7 0,15 C0,26 15,40 15,40 C15,40 30,26 30,15 C30,6.7 23.3,0 15,0 Z" fill="var(--brand-blue)"/><circle cx="15" cy="14" r="6" fill="var(--brand-green)"/></svg>
      Suite B4, Seaview Court Plaza, Harbour Road, Port Ellis
    </div>
    <div class="contact email">
      <svg width="40" height="30" viewBox="0 0 40 30" aria-hidden="true"><rect width="40" height="30" fill="var(--brand-blue)"/><path d="M0,0 L20,17 L40,0" fill="none" stroke="var(--brand-green)" stroke-width="3"/></svg>
      cedarlinecare@mailbox.com
    </div>
    <div class="contact phone">
      <svg width="44" height="36" viewBox="0 0 44 36" aria-hidden="true"><path d="M2,12 C2,4 42,4 42,12 L42,16 L32,16 L32,11 L12,11 L12,16 L2,16 Z" fill="var(--brand-blue)"/><path d="M10,18 L34,18 L40,34 L4,34 Z" fill="var(--brand-blue)"/><circle cx="22" cy="26" r="4" fill="var(--brand-green)"/></svg>
      1 555 302 4418
    </div>
    <div class="hours">MONDAY – SATURDAY 8AM TO 7PM</div>
    <div class="social">
      <div class="social-label">Visit us on</div>
      <div class="social-link"><span class="social-dot"></span>Friendsphere</div>
    </div>
  </footer>
</div>
</body>
</html>
```